I have a business that exists already (Linden Conservatory of Music) that we offer music lessons to all instruments. I recently opened a smaller version called CHORDS by Linden that will only teach piano lessons. What I'm looking for now is a 3 page Website on word press. After I choose the design I like I want to be able to take over the website and bring it to our hosting company. We want full control of it and our team will take over. The reason I'm doing this is to have other visions and ideas from others. The first page will be about the company and our message/vision. Second page about the piano lessons. The third will be about franchising this concept "Chords by Linden" Attached are 3 Logos . Please refer to our existing website www.lindenmusicconservatory.example to look at our piano page and franchising page. Please feel free to message me if you need more info. Thanks
Please note I do not want the new website (Chords by Linden) To look like the other Website (Linden Conservatory of Music) Fresh new look. I do not want the colours red or using the Red logo. I only provided it so that you have an Idea of What the other business looks like and that you can take the piano content and franchise content off of it. Chords by Linden is smaller concept and only piano lessons.
Thanks
Only Piano lessons for all students
3 page

```html
<!DOCTYPE html>
<html lang="en">
<head>
<meta charset="utf-8">
<title>Chords by Linden — Piano Lessons</title>
<link rel="stylesheet" href="https://fonts.googleapis.com/css2?family=Cinzel:wght@400;500;600&family=Montserrat:wght@400;500;600&display=swap">
<style>
:root{
  --gold:#e4c25f;
  --gold-dark:#d8b24a;
  --ink:#111111;
  --text:#2a2a2a;
  --muted:#555555;
  --blue:#1e9af0;
  --nav-active:#2a8fd6;
  --paper:#ffffff;
  --mist:#efefef;
  --night:#262626;
}
*{box-sizing:border-box;margin:0;padding:0}
html,body{width:1200px;height:2866px;overflow:hidden;background:var(--paper)}
body{position:relative;font-family:"Montserrat",sans-serif;color:var(--text)}
.block{position:absolute;left:0;width:1200px;overflow:hidden}
.heading{font-family:"Cinzel",serif;font-weight:500;color:var(--ink);letter-spacing:.5px}
.rule{display:block;width:36px;height:2px;background:var(--ink);margin-top:10px}
.rule.gold{background:var(--gold)}
.rule.center{margin-left:auto;margin-right:auto}
.btn{display:inline-block;font-family:"Cinzel",serif;font-weight:600;font-size:13px;padding:0 20px;height:35px;line-height:35px;color:var(--paper);background:var(--ink);text-decoration:none}
.btn.gold{background:var(--gold);color:var(--ink)}

/* header */
.site-header{top:0;height:92px;background:var(--paper)}
.brand{position:absolute;left:141px;top:22px;display:flex;align-items:center;gap:10px;font-family:"Cinzel",serif;font-size:30px;font-weight:500;color:var(--ink)}
.brand-square{width:14px;height:14px;background:var(--ink)}
.nav{position:absolute;right:141px;top:37px;display:flex;gap:36px;font-family:"Cinzel",serif;font-size:13.5px;letter-spacing:.5px}
.nav a{color:var(--text);text-decoration:none}
.nav a.active{color:var(--nav-active)}

/* hero */
.hero{top:92px;height:481px;background:linear-gradient(90deg,#c9b7a4 0%,#d9d3cc 35%,#eeeeee 55%,#f4f4f4 100%)}
.hero-photo{position:absolute;inset:0}
.hero-copy{position:absolute;right:144px;top:132px;text-align:right;font-family:"Cinzel",serif;color:var(--ink);font-variant:small-caps}
.hero-copy .l1{font-size:32px;line-height:40px}
.hero-copy .l2{font-size:48px;line-height:56px;font-weight:500}
.hero-copy .l3{font-size:33px;line-height:44px}
.hero-btn{position:absolute;right:142px;top:291px;height:36px;line-height:36px;padding:0 10px;background:var(--blue);color:var(--paper);font-family:"Cinzel",serif;font-size:17px;font-variant:small-caps}

/* about */
.about{top:573px;height:439px}
.about svg.band{position:absolute;inset:0}
.about-photo{position:absolute;left:141px;top:69px;width:415px;height:300px;border-radius:14px;background:linear-gradient(135deg,#6f6a62,#b3a896 50%,#3f4650)}
.about-copy{position:absolute;left:601px;top:66px;width:457px}
.about-copy h2{font-size:25px}
.about-copy h3{font-size:15px;font-weight:600;margin-top:18px;color:var(--ink)}
.about-copy p{font-size:12.6px;line-height:19px;text-align:justify;margin-top:6px}
.about-copy .btn{margin-top:14px}

/* vision */
.vision{top:1012px;height:376px;background:var(--mist);text-align:center}
.vision h2{font-size:25px;margin-top:62px}
.vision p{font-size:13.3px;line-height:22px;width:910px;margin:14px auto 0;color:var(--ink)}
.vision p+p{margin-top:4px}
.vision .btn{margin-top:16px}

/* programs */
.programs{top:1388px;height:469px}
.programs svg.band{position:absolute;inset:0}
.programs-copy{position:absolute;left:141px;top:65px;width:450px}
.programs-copy h2{font-size:25px;line-height:34px}
.perks{list-style:none;margin-top:20px}
.perks li{position:relative;padding-left:26px;font-size:12.6px;line-height:19px;margin-bottom:9px;color:var(--ink)}
.perks svg{position:absolute;left:0;top:3px}
.programs-copy .btn{margin-top:8px}
.programs-photo{position:absolute;left:644px;top:67px;width:414px;height:328px;border-radius:14px;background:linear-gradient(110deg,#1e1b18 0%,#5b5048 40%,#e9dcc8 70%,#f3ece2 100%)}

/* franchise */
.franchise{top:1857px;height:268px;background:#f0f0f0;text-align:center}
.franchise h2{font-size:32px;margin-top:62px}
.franchise p{font-size:15px;margin-top:14px;letter-spacing:.3px}
.franchise .btn{margin-top:18px}

/* booking */
.booking{top:2125px;height:477px;background:linear-gradient(180deg,#1c1c1c 0%,#2c2c2c 35%,#4a4a4a 38%,#4a4a4a 100%)}
.booking h2{color:var(--paper);font-size:24px;text-align:center;margin-top:66px}
.booking-card{position:absolute;left:141px;top:138px;width:917px;height:272px;background:var(--paper)}
.field{position:absolute;height:37px;background:var(--paper);box-shadow:0 2px 8px rgba(0,0,0,.12);font-size:11px;color:#777;padding:12px 14px}
.field.msg{height:87px}
.submit{position:absolute;left:401px;top:200px;width:115px;height:35px;line-height:35px;text-align:center;background:var(--gold);font-family:"Cinzel",serif;font-weight:600;font-size:13px;color:var(--ink)}

/* contact */
.contact{top:2602px;height:264px;background:var(--gold)}
.contact-item{position:absolute;top:44px;width:300px;text-align:center;color:var(--ink)}
.contact-item svg{display:block;margin:0 auto}
.contact-item h4{font-family:"Cinzel",serif;font-weight:500;font-size:15px;margin-top:14px}
.contact-item p{font-size:12.6px;line-height:20px;margin-top:2px}
.footer-rule{position:absolute;left:141px;top:213px;width:917px;height:1px;background:rgba(0,0,0,.25)}
.copyright{position:absolute;left:141px;top:232px;font-size:12.6px;color:var(--ink)}
.social{position:absolute;right:142px;top:223px;display:flex;gap:7px}
.social span{width:32px;height:32px;border-radius:50%;background:var(--ink)}
</style>
</head>
<body>

<header class="block site-header">
  <div class="brand"><span class="brand-square"></span>Chords by Linden</div>
  <nav class="nav">
    <a class="active" href="#">HOME</a>
    <a href="#">PIANO LESSONS</a>
    <a href="#">FRANCHISING</a>
    <a href="#">CONTACT US</a>
  </nav>
</header>

<section class="block hero">
  <div class="hero-photo" role="img" aria-label="Teacher and young student playing a white grand piano together"></div>
  <div class="hero-copy">
    <div class="l1">We Provide</div>
    <div class="l2">Piano Lessons</div>
    <div class="l3">For All Students</div>
  </div>
  <div class="hero-btn">Contact Us Today</div>
</section>

<section class="block about">
  <svg class="band" width="1200" height="439" aria-hidden="true"><polygon points="562,0 1200,0 1200,439 451,439" fill="var(--gold)"/></svg>
  <div class="about-photo" role="img" aria-label="Young man with headphones playing a keyboard in a studio"></div>
  <div class="about-copy">
    <h2 class="heading">ABOUT US</h2><span class="rule"></span>
    <h3>Playing The Piano</h3>
    <p>When you think of a piano, you probably envision black and white keys but the piano is more than those harmonious sounds created by the player. The versatility and the musicianship instilled into the player from those keys is the true magic that comes from playing piano! Starting from the grassroots, experience different methods and styles of playing piano. To mark the milestones of progression, engage in one of Linden's many unique performance opportunities like annual festival competitions, recitals or our examinations (Linden &amp; NPE). Penultimately,</p>
    <a class="btn" href="#">READ MORE</a>
  </div>
</section>

<section class="block vision">
  <h2 class="heading">OUR VISION</h2><span class="rule gold center"></span>
  <p>Our Mission Lorem ipsum dolor sit amet, consectetur adipiscing elit, sed do eiusmod tempor incididunt ut labore et dolore magna aliqua. Ut enim ad minim veniam, quis nostrud exercitation ullamco laboris nisi ut aliquip ex ea commodo consequat. Duis aute irure dolor in reprehenderit in voluptate velit esse cillum dolore eu fugiat nulla pariatur. Excepteur sint occaecat cupidatat non proident, sunt in culpa qui officia deserunt mollit anim id est laborum.</p>
  <p>Ut enim ad minim veniam, quis nostrud exercitation ullamco laboris nisi ut aliquip ex ea commodo consequat. Duis aute irure dolor in reprehenderit in voluptate velit esse cillum dolore eu fugiat nulla pariatur.</p>
  <a class="btn gold" href="#">READ MORE</a>
</section>

<section class="block programs">
  <svg class="band" width="1200" height="469" aria-hidden="true"><polygon points="0,0 720,0 826,469 0,469" fill="var(--gold)"/></svg>
  <div class="programs-copy">
    <h2 class="heading">OUR PROGRAMS ALSO PROVIDE STUDENTS THE OPPORTUNITY TO:</h2><span class="rule"></span>
    <ul class="perks">
      <li><svg width="14" height="12" viewBox="0 0 14 12"><path d="M1 6h10M7 2l4 4-4 4" fill="none" stroke="#111" stroke-width="1.5"/></svg>Participate in large-scale performances.</li>
      <li><svg width="14" height="12" viewBox="0 0 14 12"><path d="M1 6h10M7 2l4 4-4 4" fill="none" stroke="#111" stroke-width="1.5"/></svg>Perform at Linden's many community events on a regular basis.</li>
      <li><svg width="14" height="12" viewBox="0 0 14 12"><path d="M1 6h10M7 2l4 4-4 4" fill="none" stroke="#111" stroke-width="1.5"/></svg>Access the GTA's coolest Broadcast stage</li>
      <li><svg width="14" height="12" viewBox="0 0 14 12"><path d="M1 6h10M7 2l4 4-4 4" fill="none" stroke="#111" stroke-width="1.5"/></svg>Attend Clinics, Masterclasses, and Jam Nights</li>
      <li><svg width="14" height="12" viewBox="0 0 14 12"><path d="M1 6h10M7 2l4 4-4 4" fill="none" stroke="#111" stroke-width="1.5"/></svg>Access the Linden Rocks band program. Linden's Band Program empowers and electrifies students to come together, create music and confidently hit the stage with their own band identity while having fun and honing their instrument.</li>
    </ul>
    <a class="btn" href="#">READ MORE</a>
  </div>
  <div class="programs-photo" role="img" aria-label="Close-up of hands playing piano keys"></div>
</section>

<section class="block franchise">
  <h2 class="heading">FRANCHISE OPPORTUNITIES</h2>
  <p>Be Part Of The Linden Conservatory Family</p>
  <a class="btn gold" href="#">READ MORE</a>
</section>

<section class="block booking" role="img" aria-label="Dark piano keys background">
  <h2 class="heading" style="color:var(--paper)">BOOK A MEETING WITH US</h2><span class="rule gold center"></span>
  <div class="booking-card">
    <div class="field" style="left:48px;top:33px;width:266px">Your Name*</div>
    <div class="field" style="left:325px;top:33px;width:267px">Your Phone*</div>
    <div class="field" style="left:605px;top:33px;width:267px">Your Email*</div>
    <div class="field msg" style="left:48px;top:86px;width:824px">Your Message*</div>
    <div class="submit">SUBMIT</div>
  </div>
</section>

<footer class="block contact">
  <div class="contact-item" style="left:107px">
    <svg width="44" height="44" viewBox="0 0 24 24"><path d="M6.6 10.8a15 15 0 0 0 6.6 6.6l2.2-2.2c.3-.3.7-.4 1-.2 1.1.4 2.3.6 3.6.6.6 0 1 .4 1 1V20c0 .6-.4 1-1 1A17 17 0 0 1 3 4c0-.6.4-1 1-1h3.5c.6 0 1 .4 1 1 0 1.3.2 2.5.6 3.6.1.3 0 .7-.2 1z" fill="#111"/></svg>
    <h4>CALL US</h4>
    <p>1-800-555-0142</p>
  </div>
  <div class="contact-item" style="left:450px">
    <svg width="44" height="48" viewBox="0 0 24 26"><path d="M12 1a8 8 0 0 0-8 8c0 6 8 16 8 16s8-10 8-16a8 8 0 0 0-8-8zm0 11a3 3 0 1 1 0-6 3 3 0 0 1 0 6z" fill="#111"/></svg>
    <h4>POSTAL ADDRESS</h4>
    <p>123, Lorem ipsum dolor sit 123456<br>#123456 Lorem ipsum</p>
  </div>
  <div class="contact-item" style="left:760px">
    <svg width="46" height="44" viewBox="0 0 24 24"><rect x="2" y="5" width="20" height="14" rx="1" fill="#111"/><path d="M2.5 6l9.5 7 9.5-7" fill="none" stroke="#e4c25f" stroke-width="1.5"/></svg>
    <h4>E-MAIL</h4>
    <p>info@chordslindenmusic.example</p>
  </div>
  <div class="footer-rule"></div>
  <div class="copyright">Copyright 2019. Chordslinden Music Training. All rights reserved.</div>
  <div class="social"><span aria-label="Social link"></span><span aria-label="Social link"></span><span aria-label="Social link"></span></div>
</footer>

</body>
</html>
```